Change of trading name, rebrand

existing website to be updated with new theme and logo. existing website is
www.harlowbrentmere.com.au
Industry/Entity Type
Construction
Coding
Coded - Design and coding required
Number of Pages Required
5+ page
Requirements
Must have
- be mobile phone friendly

```html
<!DOCTYPE html>
<html lang="en">
<head>
<meta charset="utf-8">
<meta name="viewport" content="width=device-width, initial-scale=1">
<title>Harlow Brentmere Plant Hire</title>
<link href="https://fonts.googleapis.com/css2?family=Exo+2:wght@400;500;600;700&family=Lato:wght@400;700&display=swap" rel="stylesheet">
<style>
:root{
  --navy:#22267e;
  --navy-dark:#181b5e;
  --black:#050505;
  --white:#ffffff;
  --ink:#1d1d1d;
  --grey:#666a72;
  --light:#f3f4f8;
  --line:#d8dae4;
}
*{box-sizing:border-box;margin:0;padding:0}
html,body{width:1200px;height:3778px;overflow:hidden}
body{position:relative;background:var(--white);font-family:"Lato",sans-serif;color:var(--ink)}
.abs{position:absolute}
.head{font-family:"Exo 2",sans-serif}
a{color:inherit;text-decoration:none}

/* header */
.brand{left:110px;top:28px;width:140px;font-family:"Exo 2",sans-serif;font-weight:700;color:var(--navy);text-align:center;line-height:1}
.brand .name{font-size:40px;letter-spacing:2px}
.brand .sub{font-size:11px;letter-spacing:3px;margin-top:6px}
.contact-mini{top:38px;display:flex;gap:12px;align-items:center;font-family:"Exo 2",sans-serif}
.contact-mini .lbl{font-size:12px;color:var(--navy);font-weight:500}
.contact-mini .val{font-size:16px;color:var(--ink);margin-top:3px}
.vdiv{left:645px;top:48px;width:1px;height:24px;background:#bbb}
.quote{left:946px;top:40px;width:142px;height:45px;background:var(--navy);color:var(--white);font-family:"Exo 2",sans-serif;font-size:16px;display:flex;align-items:center;justify-content:center}

/* nav */
.nav{left:0;top:119px;width:1200px;height:60px;background:var(--navy)}
.nav-black{left:945px;top:119px;width:255px;height:60px;background:var(--black)}
.nav-active{left:84px;top:119px;width:92px;height:60px;background:var(--navy-dark)}
.nav a{position:absolute;top:22px;font-family:"Exo 2",sans-serif;font-size:13px;color:var(--white);text-transform:uppercase;white-space:nowrap}
.call-ico{left:937px;top:131px;width:36px;height:36px;border-radius:50%;background:var(--white);display:flex;align-items:center;justify-content:center}
.call-txt{left:996px;top:129px;color:var(--white);font-family:"Exo 2",sans-serif;font-size:13px;line-height:20px;font-weight:500}

/* hero */
.hero{left:0;top:179px;width:1200px;height:562px;background:linear-gradient(180deg,#8fa0b8 0%,#b6a78a 40%,#7c6a3e 70%,#5d4c2e 100%)}
.hero-shade{left:0;top:179px;width:1200px;height:562px;background:linear-gradient(180deg,rgba(20,22,50,.45),rgba(20,22,50,.1) 55%,rgba(0,0,0,.15))}
.hero-txt{left:0;width:1200px;text-align:center;color:var(--white);font-family:"Exo 2",sans-serif;text-shadow:0 2px 6px rgba(0,0,0,.5)}
.hero-btn{left:524px;top:422px;width:154px;height:49px;background:var(--white);color:var(--navy);font-family:"Exo 2",sans-serif;font-size:16px;display:flex;align-items:center;justify-content:center;box-shadow:0 3px 8px rgba(0,0,0,.3)}
.dot{top:654px;width:12px;height:12px;border-radius:50%;background:rgba(255,255,255,.45)}
.dot.on{background:var(--white)}

/* partners */
.partner{top:798px;width:104px;height:40px;border-radius:6px;background:#e5e7ef}
.arrow{top:802px}

/* about */
.about-logo{left:110px;top:960px;width:455px;height:310px;display:flex;flex-direction:column;align-items:center;justify-content:center;font-family:"Exo 2",sans-serif;font-weight:700;color:var(--navy)}
.about-logo .name{font-size:120px;letter-spacing:8px;line-height:1}
.about-logo .sub{font-size:32px;letter-spacing:12px;color:var(--black);margin-top:14px}
.h2{font-family:"Exo 2",sans-serif;font-weight:600;color:var(--navy);font-size:41px;line-height:1}
.kicker{font-family:"Exo 2",sans-serif;font-size:18px;letter-spacing:2px;color:var(--ink)}
.about-copy{left:599px;top:1015px;width:489px;font-size:18px;line-height:31px;color:var(--grey);text-align:justify}
.btn{background:var(--navy);color:var(--white);font-family:"Exo 2",sans-serif;font-size:16px;display:flex;align-items:center;justify-content:center}

/* stats */
.stats{left:0;top:1377px;width:1200px;height:297px;background:linear-gradient(90deg,#20246f,#2a2f8c 55%,#353a96)}
.stat{top:1450px;width:200px;text-align:center;color:var(--white);font-family:"Exo 2",sans-serif;font-size:16px;line-height:24px}
.stat svg{display:block;margin:0 auto 12px}

/* services */
.card{width:314px}
.card .ph{height:221px;position:relative}
.card .ico{position:absolute;right:0;bottom:0;width:68px;height:58px;background:var(--navy);display:flex;align-items:center;justify-content:center}
.card .body{padding:16px 0 0 34px}
.card h3{font-family:"Exo 2",sans-serif;font-weight:600;font-size:17px;color:var(--navy)}
.card p{font-size:11px;line-height:20px;color:var(--ink);margin-top:10px;height:40px;overflow:hidden;padding-right:8px}
.card .more{display:inline-block;margin-top:8px;font-family:"Exo 2",sans-serif;font-size:11px;font-weight:600;color:var(--navy);text-decoration:underline}
.card.hover{box-shadow:0 6px 16px rgba(0,0,0,.14);border:1px solid var(--navy);border-bottom:none;height:362px}
.card.hover .bar{position:absolute;left:18px;bottom:-4px;width:276px;height:4px;background:var(--navy)}

/* contact */
.contact-bg{left:0;top:2752px;width:1200px;height:620px;background:var(--light)}
.ci{left:110px;display:flex;gap:12px}
.ci .circ{width:62px;height:62px;border-radius:50%;background:var(--navy);display:flex;align-items:center;justify-content:center;flex:none}
.ci .lbl{font-family:"Exo 2",sans-serif;font-size:16px;color:var(--ink);margin-top:-2px}
.ci .val{font-size:16px;font-weight:700;line-height:28px;margin-top:4px}
.field{background:var(--white);box-shadow:0 1px 6px rgba(0,0,0,.08);font-size:14px;color:#666;padding:16px 18px}

/* footer */
.footer{left:0;top:3372px;width:1200px;height:406px;background:var(--navy)}
.f-brand{left:125px;top:3470px;width:183px;text-align:center;color:var(--white);font-family:"Exo 2",sans-serif;font-weight:700;line-height:1}
.f-brand .name{font-size:52px;letter-spacing:4px}
.f-brand .sub{font-size:12px;letter-spacing:5px;margin-top:8px}
.soc{top:3593px;width:32px;height:32px;border-radius:50%;background:var(--white)}
.f-col{top:3440px;color:var(--white)}
.f-col h4{font-family:"Exo 2",sans-serif;font-weight:500;font-size:19px;margin-bottom:10px}
.f-col li{list-style:none;font-size:15px;line-height:34.5px;display:flex;align-items:center;gap:10px}
.map{left:819px;top:3443px;width:269px;height:195px;background:linear-gradient(135deg,#e8eaee,#dfe4dd 50%,#ecebe6);border:1px solid #c9ccd4}
.f-line{left:110px;top:3686px;width:978px;height:1px;background:rgba(255,255,255,.55)}
.copy{left:0;top:3721px;width:1200px;text-align:center;color:var(--white);font-size:15px;font-weight:700}
</style>
</head>
<body>

<!-- header -->
<div class="abs brand"><div class="name">HBR</div><div class="sub">PLANT HIRE</div></div>

<div class="abs contact-mini" style="left:449px">
  <svg width="34" height="34" viewBox="0 0 34 34" fill="none" stroke="#22267e" stroke-width="1.6"><path d="M4 14 L17 4 L30 14 V30 H4 Z"/><path d="M4 14 L17 23 L30 14"/><circle cx="17" cy="13" r="3.5"/></svg>
  <div><div class="lbl">Send Us Email</div><div class="val">info@hbr.com.au</div></div>
</div>
<div class="abs vdiv"></div>
<div class="abs contact-mini" style="left:700px">
  <svg width="34" height="34" viewBox="0 0 34 34" fill="none" stroke="#22267e" stroke-width="1.6"><path d="M17 30 C10 20 8 16 8 12 a9 9 0 0 1 18 0 c0 4 -2 8 -9 18z"/><circle cx="17" cy="12" r="3.5"/><path d="M4 30 H30"/></svg>
  <div><div class="lbl">Location</div><div class="val">Yatala Park QLD 4299</div></div>
</div>
<a class="abs quote" href="#">GET A QUOTE</a>

<!-- nav -->
<div class="abs nav">
</div>
<div class="abs nav-active"></div>
<div class="abs nav-black"></div>
<nav class="abs" style="left:0;top:119px;width:1200px;height:60px">
  <div class="nav" style="position:absolute;left:0;top:0;width:0;height:60px;background:none">
    <a href="#" style="left:110px">Home</a>
    <a href="#" style="left:189px">About Us</a>
    <a href="#" style="left:295px">Plant Hire &#8964;</a>
    <a href="#" style="left:409px">Major Project Snapshot</a>
    <a href="#" style="left:634px">Policies</a>
    <a href="#" style="left:733px">Jobs</a>
    <a href="#" style="left:810px">Contact Us</a>
  </div>
</nav>
<div class="abs call-ico"><svg width="18" height="18" viewBox="0 0 24 24" fill="none" stroke="#22267e" stroke-width="2"><path d="M5 3h4l2 5-2.5 1.5a11 11 0 0 0 6 6L16 13l5 2v4a2 2 0 0 1-2 2A17 17 0 0 1 3 5a2 2 0 0 1 2-2z"/></svg></div>
<div class="abs call-txt">CALL US<br>1300 555 104</div>

<!-- hero -->
<div class="abs hero" role="img" aria-label="Row of yellow earthmoving machines parked on a dirt yard under a cloudy sky"></div>
<div class="abs hero-shade"></div>
<div class="abs hero-txt" style="top:228px;font-size:29px">WELCOME TO</div>
<div class="abs hero-txt head" style="top:270px;font-size:72px;font-weight:600;letter-spacing:1px">HARLOW BRENTMERE</div>
<div class="abs hero-txt" style="top:370px;font-size:24px;letter-spacing:5px">PLANT HIRE</div>
<a class="abs hero-btn" href="#">GET STARTED</a>
<div class="abs dot" style="left:559px"></div>
<div class="abs dot on" style="left:607px"></div>
<div class="abs dot" style="left:632px"></div>
<svg class="abs" style="left:0;top:670px" width="1200" height="80" viewBox="0 0 1200 80">
  <path d="M0 16 H460 L510 62 H1200 V80 H0 Z" fill="#ffffff"/>
  <path d="M0 2 H466 L514 46 H1200 V54 H510 L462 10 H0 Z" fill="#22267e"/>
  <path d="M0 14 H456 L506 60 H1200 V66 H502 L452 20 H0 Z" fill="#22267e"/>
</svg>

<!-- partners -->
<svg class="abs arrow" style="left:44px" width="20" height="32" viewBox="0 0 20 32" fill="none" stroke="#888" stroke-width="2.5"><path d="M16 3 L4 16 L16 29"/></svg>
<div class="abs partner" style="left:112px"></div>
<div class="abs partner" style="left:256px"></div>
<div class="abs partner" style="left:401px"></div>
<div class="abs partner" style="left:546px"></div>
<div class="abs partner" style="left:692px"></div>
<div class="abs partner" style="left:836px"></div>
<div class="abs partner" style="left:981px"></div>
<svg class="abs arrow" style="left:1134px" width="20" height="32" viewBox="0 0 20 32" fill="none" stroke="#888" stroke-width="2.5"><path d="M4 3 L16 16 L4 29"/></svg>

<!-- about -->
<div class="abs about-logo"><div class="name">HBR</div><div class="sub">PLANT HIRE</div></div>
<h2 class="abs h2" style="left:599px;top:922px">ABOUT HBR</h2>
<div class="abs kicker" style="left:599px;top:978px">PLANT HIRE</div>
<div class="abs about-copy">
  <p>Harlow Brentmere Heavy Equipment Hire specialise in the hire of heavy earthmoving, mining and construction machines with specialised attachments and tooling.</p>
  <p style="margin-top:31px">Our array of machines and attachments is second to none, and we have one of the largest hire fleets available in South East Queensland.</p>
</div>
<a class="abs btn" href="#" style="left:599px;top:1251px;width:155px;height:49px">READ MORE</a>

<!-- stats -->
<div class="abs stats" role="img" aria-label="Navy tinted band over a faint photo of heavy machinery"></div>
<div class="abs stat" style="left:69px">
  <svg width="80" height="80" viewBox="0 0 80 80" fill="#fff"><circle cx="40" cy="30" r="10"/><circle cx="20" cy="36" r="8"/><circle cx="60" cy="36" r="8"/><path d="M24 72 a16 18 0 0 1 32 0z"/><path d="M6 74 a14 16 0 0 1 22-10 v10z"/><path d="M74 74 a14 16 0 0 0-22-10 v10z"/><path d="M22 6l3 6 6 1-4.5 4 1 6-5.5-3-5.5 3 1-6-4.5-4 6-1z M40 2l3 6 6 1-4.5 4 1 6-5.5-3-5.5 3 1-6-4.5-4 6-1z M58 6l3 6 6 1-4.5 4 1 6-5.5-3-5.5 3 1-6-4.5-4 6-1z"/></svg>
  20+<br>Years of experience
</div>
<div class="abs stat" style="left:274px">
  <svg width="86" height="86" viewBox="0 0 86 86" fill="none" stroke="#fff" stroke-width="4"><rect x="6" y="44" width="34" height="16"/><rect x="14" y="32" width="16" height="12"/><path d="M36 44 L62 14 L78 34"/><path d="M78 34 l-8 14 h10z" fill="#fff"/><rect x="4" y="62" width="44" height="12" rx="6"/></svg>
  100+<br>Machines in fleet
</div>
<div class="abs stat" style="left:487px">
  <svg width="80" height="80" viewBox="0 0 80 80" fill="#fff"><circle cx="40" cy="30" r="10"/><circle cx="20" cy="36" r="8"/><circle cx="60" cy="36" r="8"/><path d="M24 72 a16 18 0 0 1 32 0z"/><path d="M6 74 a14 16 0 0 1 22-10 v10z"/><path d="M74 74 a14 16 0 0 0-22-10 v10z"/><path d="M22 6l3 6 6 1-4.5 4 1 6-5.5-3-5.5 3 1-6-4.5-4 6-1z M40 2l3 6 6 1-4.5 4 1 6-5.5-3-5.5 3 1-6-4.5-4 6-1z M58 6l3 6 6 1-4.5 4 1 6-5.5-3-5.5 3 1-6-4.5-4 6-1z"/></svg>
  One of qld's largest<br>suppliers
</div>
<div class="abs stat" style="left:701px">
  <svg width="86" height="86" viewBox="0 0 86 86" fill="none" stroke="#fff" stroke-width="9"><circle cx="43" cy="43" r="26"/><path d="M43 6v12M43 68v12M6 43h12M68 43h12M17 17l8 8M61 61l8 8M17 69l8-8M61 25l8-8"/><path d="M36 50 L52 34" stroke-width="6"/><circle cx="54" cy="32" r="6" stroke-width="4"/></svg>
  Onsite servicing
</div>
<div class="abs stat" style="left:915px">
  <svg width="104" height="80" viewBox="0 0 104 80" fill="none" stroke="#fff" stroke-width="4"><rect x="4" y="4" width="96" height="70" rx="4"/><path d="M4 18 H100"/><circle cx="52" cy="44" r="10"/><path d="M52 28v6M52 54v6M36 44h6M62 44h6"/><path d="M10 44 h18 M76 44 h18"/></svg>
  Custom Machine<br>Attachments
</div>

<!-- services -->
<h2 class="abs h2" style="left:0;width:1200px;text-align:center;top:1729px">OUR SERVICES</h2>
<div class="abs kicker" style="left:0;width:1200px;text-align:center;top:1786px">WE OFFER</div>

<div class="abs card" style="left:110px;top:1840px">
  <div class="ph" role="img" aria-label="Excavator digging on a school building site" style="background:linear-gradient(160deg,#8fb3d6,#c98a5a 55%,#8b6e4e)"><div class="ico"><svg width="34" height="30" viewBox="0 0 34 30" fill="none" stroke="#fff" stroke-width="2"><rect x="3" y="14" width="14" height="8"/><path d="M15 14 L22 4 L30 12 L27 18"/><rect x="2" y="23" width="20" height="5" rx="2.5"/></svg></div></div>
  <div class="body"><h3>EXCAVATORS</h3><p>With one of the largest fleet of excavators for hire in South East Queensland, at HBR Heavy Equipment.</p><a class="more" href="#">READ MORE</a></div>
</div>
<div class="abs card hover" style="left:443px;top:1840px">
  <div class="ph" role="img" aria-label="Yellow dozer parked on a grassy yard" style="background:linear-gradient(160deg,#7fb1e3,#c9a64a 50%,#8c7a3f)"><div class="ico"><svg width="36" height="30" viewBox="0 0 36 30" fill="none" stroke="#fff" stroke-width="2"><rect x="10" y="8" width="12" height="10"/><rect x="6" y="20" width="24" height="6" rx="3"/><path d="M6 12 L2 26"/><path d="M30 18 l4 6"/></svg></div></div>
  <div class="body"><h3>DOZER HIRE</h3><p>We have Kovarr and Caldera dozers for hire - in a range of sizes suitable.</p><a class="more" href="#">READ MORE</a></div>
  <div class="bar"></div>
</div>
<div class="abs card" style="left:774px;top:1840px">
  <div class="ph" role="img" aria-label="Articulated dump truck on a gravel site" style="background:linear-gradient(160deg,#5fa0e0,#b68d3a 55%,#80683a)"><div class="ico"><svg width="36" height="30" viewBox="0 0 36 30" fill="none" stroke="#fff" stroke-width="2"><path d="M4 8 H22 L20 20 H4 Z"/><rect x="22" y="12" width="10" height="8"/><circle cx="9" cy="24" r="3"/><circle cx="27" cy="24" r="3"/></svg></div></div>
  <div class="body"><h3>DUMP TRUCK HIRE</h3><p>We are South East Queensland's material cartage and haulage specialists, with a range of road registered,</p><a class="more" href="#">READ MORE</a></div>
</div>

<div class="abs card" style="left:110px;top:2234px">
  <div class="ph" role="img" aria-label="Yellow grader in a car park" style="background:linear-gradient(160deg,#7ab2e2,#c9a84e 55%,#7d7b73)"><div class="ico"><svg width="38" height="28" viewBox="0 0 38 28" fill="none" stroke="#fff" stroke-width="2"><rect x="24" y="6" width="10" height="10"/><path d="M2 16 H34"/><path d="M14 16 L10 22 H20"/><circle cx="6" cy="22" r="3"/><circle cx="28" cy="22" r="3"/></svg></div></div>
  <div class="body"><h3>GRADER HIRE</h3><p>Precision, skill and productivity are the hallmarks of our road grading services, we operate an extensive</p><a class="more" href="#">READ MORE</a></div>
</div>
<div class="abs card" style="left:443px;top:2234px">
  <div class="ph" role="img" aria-label="Loader beside stacked black pipes" style="background:linear-gradient(160deg,#6fa8e0,#40404a 55%,#b05a2a)"><div class="ico"><svg width="38" height="28" viewBox="0 0 38 28" fill="none" stroke="#fff" stroke-width="2"><rect x="8" y="4" width="12" height="10"/><path d="M4 14 H28 V20 H4Z"/><path d="M28 14 L34 10 V18"/><circle cx="10" cy="22" r="3"/><circle cx="24" cy="22" r="3"/></svg></div></div>
  <div class="body"><h3>LOADER HIRE</h3><p>We have Kovarr and Caldera dozers for hire - in a range of sizes suitable for projects from detailed</p><a class="more" href="#">READ MORE</a></div>
</div>
<div class="abs card" style="left:774px;top:2234px">
  <div class="ph" role="img" aria-label="Yellow skid steer loader on concrete" style="background:linear-gradient(160deg,#aab6c0,#c7a23c 50%,#5a5a52)"><div class="ico"><svg width="38" height="28" viewBox="0 0 38 28" fill="none" stroke="#fff" stroke-width="2"><rect x="10" y="4" width="12" height="14"/><path d="M22 8 L32 14 L32 20 L26 20"/><circle cx="12" cy="22" r="3"/><circle cx="22" cy="22" r="3"/></svg></div></div>
  <div class="body"><h3>BOBCAT HIRE</h3><p>Our compact earthmoving range comprises of a large number of diverse and flexible machines</p><a class="more" href="#">READ MORE</a></div>
</div>

<a class="abs btn" href="#" style="left:522px;top:2620px;width:154px;height:48px">VIEW MORE</a>

<!-- contact -->
<div class="abs contact-bg"></div>
<h2 class="abs h2" style="left:0;width:1200px;text-align:center;top:2816px">GET IN TOUCH WITH US</h2>
<div class="abs kicker" style="left:0;width:1200px;text-align:center;top:2873px">CONTACT US</div>

<div class="abs ci" style="top:2932px">
  <div class="circ"><svg width="22" height="22" viewBox="0 0 24 24" fill="#fff"><path d="M12 22 C6 14 5 11 5 9 a7 7 0 0 1 14 0 c0 2 -1 5 -7 13z"/><circle cx="12" cy="9" r="2.6" fill="#22267e"/></svg></div>
  <div><div class="lbl">LOCATION</div><div class="val">18 Wattle Ridge Rd,<br>Yatala Park QLD 4299</div></div>
</div>
<div class="abs ci" style="top:3066px">
  <div class="circ"><svg width="22" height="22" viewBox="0 0 24 24" fill="#fff"><path d="M5 3h4l2 5-2.5 1.5a11 11 0 0 0 6 6L16 13l5 2v4a2 2 0 0 1-2 2A17 17 0 0 1 3 5a2 2 0 0 1 2-2z"/></svg></div>
  <div><div class="lbl">PHONE NUMBER</div><div class="val">1300 555 104</div></div>
</div>
<div class="abs ci" style="top:3180px">
  <div class="circ"><svg width="24" height="20" viewBox="0 0 24 20" fill="#fff"><rect x="1" y="2" width="22" height="16" rx="2"/><path d="M2 4 L12 11 L22 4" stroke="#22267e" stroke-width="2" fill="none"/></svg></div>
  <div><div class="lbl">EMAIL ADDRESS</div><div class="val">info@hbr.com.au</div></div>
</div>

<div class="abs field" style="left:414px;top:2931px;width:331px;height:50px">First Name</div>
<div class="abs field" style="left:757px;top:2931px;width:331px;height:50px">Your Email</div>
<div class="abs field" style="left:414px;top:2994px;width:331px;height:50px">Your Phone</div>
<div class="abs field" style="left:757px;top:2994px;width:331px;height:50px">Address</div>
<div class="abs field" style="left:414px;top:3059px;width:674px;height:111px">Message</div>
<a class="abs btn" href="#" style="left:411px;top:3202px;width:154px;height:48px">SUBMIT</a>

<!-- footer -->
<svg class="abs" style="left:0;top:3306px" width="1200" height="70" viewBox="0 0 1200 70">
  <path d="M0 44 H470 L516 8 H1200 V70 H0 Z" fill="#22267e"/>
  <path d="M0 32 H462 L508 0 H1200 V6 H512 L466 38 H0 Z" fill="#22267e"/>
</svg>
<div class="abs footer"></div>
<div class="abs f-brand"><div class="name">HBR</div><div class="sub">PLANT HIRE</div></div>
<a class="abs soc" href="#" aria-label="Social link" style="left:113px"></a>
<a class="abs soc" href="#" aria-label="Social link" style="left:170px"></a>
<a class="abs soc" href="#" aria-label="Social link" style="left:229px"></a>
<a class="abs soc" href="#" aria-label="Social link" style="left:286px"></a>

<div class="abs f-col" style="left:403px">
  <h4>QUICK LINKS</h4>
  <ul>
    <li>&#10140; Home</li><li>&#10140; About</li><li>&#10140; Plant Hire</li><li>&#10140; Jobs</li><li>&#10140; Contact Us</li>
  </ul>
</div>
<div class="abs f-col" style="left:619px">
  <h4>HELP LINKS</h4>
  <ul>
    <li>&#10140; FAQ</li><li>&#10140; Terms of use</li><li>&#10140; Privacy Policy</li><li>&#10140; Support Links</li><li>&#10140; Conditions</li>
  </ul>
</div>
<div class="abs map" role="img" aria-label="Street map showing the yard location"></div>
<div class="abs f-line"></div>
<div class="abs copy">Copyrights@2024.HBR.All Rights Reserved</div>

</body>
</html>
```